Banner ad design for Vorlix Display Ads

We are looking for a designer to develop a concept for banner ads for a Vorlix Display campaign we are building.

We have 3 business lines, shredding services, records management services and scanning services.

We are looking for 4 sets of ads to be created, one for each business line + one set that showcases all of our lines together.

For the design concepts, we would like to see a few sizes (banner, square, leaderboard, skyscraper, etc) for each.

The person chosen will then need to create the ads into all Vorlix supported sizes -- 20 sizes total for each set of ads as per the Vorlix size guidelines found on this page - https://help.vorlix.com/vorlix-ads/answer/5830417?hl=en&ref_topic=6402871#

A few items to note:
- Design should complement our existing brand/website look and feel (www.tamrock-dunes.ca)
- Each final ad must be 150Kb or less in size
- Final designs should be editable, meaning if we would like to change some copy in the design, we can do so using a well-known software (Canva, Photoshop/InDesign, etc)
- Some images are attached for use, but if you feel a different stock image is more suitable to to your design, please go ahead and use it.

Provided below is some messaging that can be used for each set of ads. Do not feel you need to use all of the messaging, it is provided for guidance.

SHREDDING SERVICES:

Possible Short Headline:
-- One-Time Shredding Services
-- Secure Shredding Services
-- Affordable On-Site Shredding

Possible Long Headline
-- Your Paper Can be Destroyed as Soon as the Next Business Day

Possible Descriptions:
-- TORV QQQ Certified On site shredding company. Service as soon as Next Day.
-- Secure and Affordable Toronto & GTA On-Site Shredding.
-- Certified, Affordable Office Shredding Since 2003.
-- Quick, no contact and affordable paper shredding services in Toronto & Southern Ontario.
-- Certified, Affordable Office Shredding Since 2003. Fast, no contact shredding service.

Call to Action
-- Get a Quote

RECORDS MANAGEMENT
Short Headline:
-- Off-site Records Storage
-- Records Management & Storage
-- Secure Records Storage
-- Records Management Services
-- Long Term Records Management
-- Document Storage Solutions

Possible Description
-- Local, Affordable Storage Solutions. Protect and Store your Documents in our Secure Facility
-- Local, Affordable Records Management Solutions. Store your Records in our Secure Facility
-- Certified, Affordable Document Storage Since 2004. Contact Us for a Free Quote!
-- Veltra+ Certified, Affordable Document Storage Since 2004. Contact Us for a Free Quote!

Call to Action
-- Get a Quote

SCANNING SERVICES

Short Headline:
-- Professional Scanning Company
-- Toronto & GTA Scanning Service
-- Document Scanning Services
-- Digital Conversion Services
-- Fast & Easy Retrieval

Description
-- Scan and documents and files with Professional scanning services from Tamrock-Dunes
-- Convert Your Paper Files to Electronic Files. Fast & Easy Retrieval.
-- Easily access your documents electronically with Document Scanning Services

Call to Action
-- Get a Quote

ALL SERVICES AD SET
Short Headline
-- Shred, Scan & Store Documents
-- Secure Shredding, Records Management and Scanning Services
-- #1 Document Management Company
-- Tamrock Dunes Shredding, Storage & Scanning

Description
-- Secure and Affordable Toronto & GTA On-Site Shredding, Document Storage & Scanning Company

Call to Action
-- Get a Quote

Font styles to use
Sans Serif

```html
<!DOCTYPE html>
<html lang="en">
<head>
<meta charset="utf-8">
<title>Tamrock-Dunes Scanning Services – Leaderboard</title>
<link rel="stylesheet" href="https://fonts.googleapis.com/css2?family=Arimo:wght@400;700&family=Roboto+Condensed:wght@700&display=swap">
<style>
  :root {
    --white: #ffffff;
    --brand-navy: #12356b;
    --panel-blue-light: #22a5e3;
    --panel-blue-dark: #0f7fc6;
    --accent-green: #27d46a;
    --accent-green-dark: #17b457;
    --tagline-ink: #1f2f4a;
    --copy-navy: #0f2a5c;
    --photo-light: #c9c4bf;
    --photo-dark: #4d5156;
  }
  * { margin: 0; padding: 0; box-sizing: border-box; }
  html, body { width: 1200px; height: 148px; overflow: hidden; background: var(--white); }
  .banner {
    position: relative;
    width: 1200px;
    height: 148px;
    overflow: hidden;
    background: var(--white);
    font-family: "Arimo", Arial, sans-serif;
  }
  .brand {
    position: absolute;
    left: 30px;
    top: 52px;
    width: 230px;
  }
  .brand-name {
    display: flex;
    align-items: center;
    gap: 8px;
    font-weight: 700;
    font-size: 25px;
    letter-spacing: -0.5px;
    color: var(--brand-navy);
    line-height: 1;
  }
  .brand-dot {
    width: 14px; height: 14px;
    border-radius: 50%;
    background: var(--panel-blue-light);
    flex: none;
  }
  .brand-tagline {
    margin-top: 6px;
    font-size: 19px;
    color: var(--tagline-ink);
    line-height: 1;
  }
  .staff-photo {
    position: absolute;
    left: 268px;
    top: 0;
    width: 340px;
    height: 148px;
    background: linear-gradient(100deg, var(--photo-light) 0%, #a9a5a2 45%, var(--photo-dark) 100%);
  }
  .panel-shape {
    position: absolute;
    left: 0; top: 0;
    width: 1200px; height: 148px;
  }
  .headline {
    position: absolute;
    left: 640px;
    top: 20px;
    width: 220px;
    text-align: center;
    font-family: "Roboto Condensed", Arial, sans-serif;
    font-weight: 700;
    font-size: 34px;
    line-height: 1.08;
    color: var(--white);
    letter-spacing: 0.3px;
  }
  .description {
    position: absolute;
    left: 872px;
    top: 22px;
    width: 170px;
    text-align: center;
    font-size: 19px;
    line-height: 1.1;
    color: var(--copy-navy);
  }
  .cta {
    position: absolute;
    left: 1063px;
    top: 30px;
    width: 108px;
    height: 88px;
    border-radius: 10px;
    background: var(--accent-green);
    color: var(--white);
    font-size: 22px;
    line-height: 1.25;
    text-align: center;
    display: flex;
    align-items: center;
    justify-content: center;
    text-decoration: none;
  }
</style>
</head>
<body>
  <div class="banner">
    <div class="brand">
      <div class="brand-name"><span class="brand-dot"></span>tamrock-dunes</div>
      <div class="brand-tagline">Information Security</div>
    </div>

    <div class="staff-photo" role="img" aria-label="Photo of a staff member at an office desk handling a stack of paper documents for scanning"></div>

    <svg class="panel-shape" viewBox="0 0 1200 148" aria-hidden="true">
      <defs>
        <linearGradient id="panelBlue" x1="0" y1="0" x2="1" y2="0">
          <stop offset="0" stop-color="var(--panel-blue-light)"/>
          <stop offset="1" stop-color="var(--panel-blue-dark)"/>
        </linearGradient>
      </defs>
      <polygon points="596,0 610,0 590,148 576,148" fill="var(--accent-green)"/>
      <polygon points="610,0 1200,0 1200,148 590,148" fill="url(#panelBlue)"/>
    </svg>

    <h1 class="headline">FAST &amp;<br>EASY<br>RETRIEVAL</h1>

    <p class="description">Easily access your documents electronically with Document Scanning Services</p>

    <a class="cta" href="#">Get a<br>Quote</a>
  </div>
</body>
</html>
```